Medical consulting firm needs polished website

I am a physician and working on setting up a smal consulting firm in New Hampshire, USA. It is called Bright Harbor Medical Services, LLC and the website will be BrightHarborMed.com. I was puttering around at making my own website, and it just didn't come together nicely so I've decided to leave it to the pros. The focus of the business is Advanced Care Planning, ie planning for your future medical needs. So it deals with some heavy stuff like planning for if you get sick, who should make decisions for you, end of life options etc. So it can't be too flippant or cutesy, but also can't be too dour and dark. I am hoping to convey that by thinking ahead and making some plans you can lift some of the worries off of yourself and your family - and that we can help make a scary sounding path more manageable. I want it to be made with wordpress and I have actually already bought a template ( Vitarun – A Modern Multidisciplinary Medical & Health Theme ). The website needs to have general information about our services, doc profile, appointment maker, blog/url link page, and ideally web commerce application ( the template has access to woocommerce). I've posted my business card and current brochure (still tweaking them, but you get the idea). I am also partnering with lumenfold.com and so have included their logo and would want connections/info about them. I have the logos etc in different formats as needed.

Target Market(s)

middle aged to older adults

Industry/Entity Type

Medical

Coding

Coded - Design and coding required

Font styles to use
Sans Serif

Requirements
Must have
• as above.
Nice to have
• Ease of reading/access for elderly viewers. woo commerce.

```html
<!DOCTYPE html>
<html lang="en">
<head>
<meta charset="utf-8">
<title>Bright Harbor Medical Services</title>
<link href="https://fonts.googleapis.com/css2?family=Open+Sans:wght@400;600;700&display=swap" rel="stylesheet">
<style>
:root{
  --blue:#2378c3;
  --blue-dark:#1a63a6;
  --ink:#222529;
  --text:#777b80;
  --line:#e3e5e8;
  --soft:#f4f5f6;
  --panel:#efeff1;
  --white:#ffffff;
}
*{box-sizing:border-box;margin:0;padding:0}
html,body{width:1200px;height:3147px;overflow:hidden}
body{font-family:"Open Sans",Arial,sans-serif;color:var(--ink);background:var(--white);position:relative}
.abs{position:absolute}
p.small{font-size:11px;line-height:22px;color:var(--text)}

/* header */
.site-header{position:absolute;left:0;top:0;width:1200px;height:128px}
.brand{left:132px;top:40px;display:flex;align-items:center;gap:12px}
.brand-mark{width:40px;height:40px;border-radius:50%;background:var(--blue)}
.brand-name{font-size:26px;font-weight:600;color:var(--blue);line-height:1}
.info{top:46px;display:flex;gap:14px;align-items:flex-start;font-size:12.5px;line-height:22px;color:#444}
.info svg{flex:none;margin-top:4px}
.main-nav{position:absolute;left:0;top:128px;width:1200px;height:57px;border-top:1px solid var(--line);border-bottom:1px solid var(--line)}
.main-nav a{position:absolute;top:19px;font-size:11.5px;font-weight:600;color:#333;text-decoration:none;letter-spacing:.2px}
.main-nav a.current{color:var(--blue)}
.btn-book{position:absolute;left:873px;top:2px;width:194px;height:52px;background:var(--blue);color:#fff;font-size:11.5px;font-weight:600;display:flex;align-items:center;justify-content:center}

/* hero */
.hero{position:absolute;left:0;top:185px;width:1200px;height:430px;background:linear-gradient(90deg,#f3f3f4 0%,#ececee 50%,#dfe1e4 100%)}
.hero-photo{position:absolute;left:100px;top:0;width:920px;height:430px;background:radial-gradient(ellipse at 78% 40%,#f2ede8 0%,#e6e2df 40%,rgba(230,230,232,0) 72%)}
.hero-title{left:132px;top:82px;font-size:47px;font-weight:600;line-height:58px;color:#333;letter-spacing:.5px}
.btn-primary{background:var(--blue);color:#fff;font-size:12px;font-weight:600;display:flex;align-items:center;justify-content:center}
.hero .btn-primary{left:132px;top:222px;width:155px;height:51px}

/* intro */
.intro-photo{top:668px;width:285px;height:167px;background:linear-gradient(135deg,#dfe9f2,#b8cfe2)}
.card-title{font-size:17px;font-weight:700;letter-spacing:.3px}
.accordion{left:749px;top:670px;width:318px}
.accordion .item{background:var(--panel);height:50px;padding:0 18px;display:flex;align-items:center;font-size:13px;color:#333;margin-bottom:6px}
.accordion .body{padding:8px 18px 20px}

/* services */
.services{position:absolute;left:0;top:1040px;width:1200px;height:603px;background:var(--soft)}
.section-title{position:absolute;left:0;width:1200px;text-align:center;font-size:28px;font-weight:700}
.section-sub{position:absolute;left:300px;width:600px;text-align:center;font-size:11px;line-height:24px;color:var(--text)}
.service-card{top:220px;width:283px;height:318px;background:#fff;text-align:center;box-shadow:0 1px 3px rgba(0,0,0,.05)}
.service-card svg{margin-top:38px}
.service-card h3{margin-top:30px;font-size:17px;font-weight:700}
.service-card p{padding:14px 30px 0}
.arrow{color:#c5c7ca}

/* testimonial */
.testimonial{position:absolute;left:0;top:1643px;width:1200px;height:355px;background:linear-gradient(90deg,#e9edf2 0%,#eef0f3 60%,#f1f2f4 100%)}
.testimonial-photo{position:absolute;left:0;top:0;width:640px;height:355px;background:linear-gradient(90deg,#c9a995 0%,#b3c9dc 45%,rgba(238,240,243,0) 100%)}
.quote-mark{left:522px;top:40px;font-size:110px;line-height:110px;color:#c9ccd0;font-family:Georgia,serif}
.testimonial p{left:525px;top:148px;width:545px}
.author{left:525px;top:220px;font-size:12px;font-style:italic;color:var(--blue)}

/* news */
.news-card{top:2190px;width:289px;height:448px;background:var(--soft)}
.news-photo{height:188px;background:linear-gradient(135deg,#dde7ef,#a9c4dc)}
.date{position:absolute;left:20px;top:208px;width:64px;height:32px;background:var(--blue);color:#fff;font-size:9.5px;display:flex;align-items:center;justify-content:center}
.news-card h3{position:absolute;left:20px;top:268px;font-size:17px;font-weight:700}
.news-card p{position:absolute;left:20px;top:300px;width:255px}
.byline{position:absolute;left:20px;top:392px;display:flex;align-items:center;gap:14px;font-size:10.5px;font-weight:600;color:#333}
.avatar{width:30px;height:30px;border-radius:50%;background:#d9b8a4}

/* footer */
.site-footer{position:absolute;left:0;top:2677px;width:1200px;height:398px;background:var(--soft)}
.footer-head{font-size:15px;font-weight:700;color:var(--blue)}
.contact-line{display:flex;gap:14px;font-size:12px;line-height:21px;color:#444}
.tweet{display:flex;gap:24px}
.tweet .dot{width:10px;height:10px;border-radius:50%;background:var(--blue);flex:none;margin-top:12px}
.post{display:flex;gap:22px}
.post .avatar{width:52px;height:52px;flex:none;background:#d8c3b5}
.divider{height:1px;background:#d9dbde}
.bottom-bar{position:absolute;left:0;top:3075px;width:1200px;height:72px;border-top:1px solid var(--line);background:#fff}
.social{left:370px;top:30px;display:flex;gap:14px}
.social span{width:12px;height:12px;border-radius:50%;background:#555}
.partner{left:875px;top:22px;display:flex;align-items:center;gap:10px;font-size:24px;font-weight:600;color:#1f3b63}
.partner i{width:26px;height:26px;border-radius:50%;background:#1f3b63}
</style>
</head>
<body>

<header class="site-header">
  <div class="abs brand"><span class="brand-mark"></span><span class="brand-name">Bright Harbor</span></div>
  <div class="abs info" style="left:445px">
    <svg width="24" height="24" viewBox="0 0 24 24" fill="none" stroke="#2378c3" stroke-width="1.5"><circle cx="12" cy="12" r="10"/><path d="M12 6v6l4 2"/></svg>
    <div>Monday - Friday 08:00 - 20:00<br>Saturday and Sunday - CLOSED</div>
  </div>
  <div class="abs info" style="left:705px">
    <svg width="18" height="26" viewBox="0 0 18 26" fill="none" stroke="#2378c3" stroke-width="1.5"><rect x="2" y="1" width="14" height="24" rx="2"/><path d="M7 21h4"/></svg>
    <div>603-555-0142<br>info@brightharbormed.co</div>
  </div>
  <div class="abs info" style="left:915px">
    <svg width="20" height="26" viewBox="0 0 20 26" fill="none" stroke="#2378c3" stroke-width="1.5"><path d="M10 25s8-9 8-15a8 8 0 0 0-16 0c0 6 8 15 8 15z"/><circle cx="10" cy="10" r="3"/></svg>
    <div>12 Elm Street<br>Concord, NH 03301</div>
  </div>
</header>

<nav class="main-nav">
  <a class="current" style="left:133px">HOME</a>
  <a style="left:210px">ABOUT US</a>
  <a style="left:307px">SERVICES</a>
  <a style="left:402px">TESTIMONIALS</a>
  <a style="left:527px">NEWS</a>
  <a style="left:603px">CONTACT US</a>
  <div class="btn-book">BOOK APPOINTMENT</div>
</nav>

<section class="hero">
  <div class="hero-photo" role="img" aria-label="Smiling older woman exercising with hand weights"></div>
  <h1 class="abs hero-title">ADVANCED CARE<br>PLANNING</h1>
  <div class="abs btn-primary">VIEW DETAILS</div>
  <svg class="abs" style="left:78px;top:185px" width="16" height="40" viewBox="0 0 16 40" fill="none" stroke="#c5c7ca" stroke-width="1.5"><path d="M14 2L2 20l12 18"/></svg>
  <svg class="abs" style="left:1090px;top:185px" width="16" height="40" viewBox="0 0 16 40" fill="none" stroke="#c5c7ca" stroke-width="1.5"><path d="M2 2l12 18L2 38"/></svg>
</section>

<section class="intro">
  <div class="abs intro-photo" style="left:132px" role="img" aria-label="Doctor working at a laptop in a bright clinic"></div>
  <h3 class="abs card-title" style="left:132px;top:858px">ADVANCED CARE</h3>
  <p class="abs small" style="left:132px;top:892px;width:290px">Nemo enim ipsam voluptatem quia voluptas sit aspernatur aut odit aut fugit, sed quia consequuntur magni dolores eos qui ratione voluptatem sequi nesciunt.</p>
  <div class="abs intro-photo" style="left:443px" role="img" aria-label="Smiling doctor with a stethoscope"></div>
  <h3 class="abs card-title" style="left:447px;top:858px">FUTURE MEDICAL</h3>
  <p class="abs small" style="left:443px;top:892px;width:290px">Nemo enim ipsam voluptatem quia voluptas sit aspernatur aut odit aut fugit, sed quia consequuntur magni dolores eos qui ratione voluptatem sequi nesciunt.</p>

  <div class="abs accordion">
    <div class="item" style="margin-bottom:0">ADVANCED CARE PLANNING</div>
    <div class="body"><p class="small" style="font-size:10px;line-height:24px">Nemo enim ipsam voluptatem quia voluptas sit aspernatur aut odit aut fugit, sed quia consequuntur magni dolores eos qui ratione voluptatem sequi nesciunt.</p></div>
    <div class="item">HIGHEST QUALITY HEALTHCARE</div>
    <div class="item">IMPROVING THE QUALITY OF YOUR LIFE</div>
    <div class="item">LEADING THE WAY IN MEDICAL</div>
  </div>
</section>

<section class="services">
  <h2 class="section-title" style="top:52px">OUR SERVICES</h2>
  <p class="section-sub" style="top:120px">Lorem ipsum dolor sit amet, consectetuer. Proin gravida nibh vel velit auctor aliquetenean. Cum sociis Theme natoque penatibus et magnis dis parturient nascetur ridiculus mus.</p>

  <div class="abs service-card" style="left:132px">
    <svg width="54" height="76" viewBox="0 0 54 76" fill="none" stroke="#2378c3" stroke-width="3"><rect x="3" y="8" width="48" height="65" rx="2"/><rect x="17" y="3" width="20" height="10" fill="#fff"/><path d="M13 28h28M13 38h28M13 48h28M13 58h28"/></svg>
    <h3>HEALTHCARE PLANNING</h3>
    <p class="small">Lorem ipsum dolor sit amet, consectetuer. Proin gravida nibh vel velit auctor aliquet. Aenean sollicitudi.</p>
  </div>
  <div class="abs service-card" style="left:459px">
    <svg width="70" height="76" viewBox="0 0 70 76" fill="none" stroke="#2378c3" stroke-width="4" stroke-linecap="round"><path d="M14 14l42 42M22 34l14-14M30 42l14-14M46 58l12 12M8 8l12 12M4 20L20 4M50 66l16-16"/></svg>
    <h3>MEDICAL SITUATIONS</h3>
    <p class="small">Lorem ipsum dolor sit amet, consectetuer. Proin gravida nibh vel velit auctor aliquet. Aenean sollicitudi.</p>
  </div>
  <div class="abs service-card" style="left:786px">
    <svg width="50" height="76" viewBox="0 0 50 76"><path d="M25 4C25 4 4 34 4 50a21 21 0 0 0 42 0C46 34 25 4 25 4z" fill="#2378c3"/><path d="M14 50a11 11 0 0 0 11 11" fill="none" stroke="#fff" stroke-width="3"/></svg>
    <h3>BINDING DIRECTIVES</h3>
    <p class="small">Lorem ipsum dolor sit amet, consectetuer. Proin gravida nibh vel velit auctor aliquet. Aenean sollicitudi.</p>
  </div>
  <svg class="abs" style="left:80px;top:360px" width="16" height="40" viewBox="0 0 16 40" fill="none" stroke="#c5c7ca" stroke-width="1.5"><path d="M14 2L2 20l12 18"/></svg>
  <svg class="abs" style="left:1098px;top:360px" width="16" height="40" viewBox="0 0 16 40" fill="none" stroke="#c5c7ca" stroke-width="1.5"><path d="M2 2l12 18L2 38"/></svg>
</section>

<section class="testimonial">
  <div class="testimonial-photo" role="img" aria-label="Smiling older man in a light blue shirt"></div>
  <div class="abs quote-mark">&ldquo;</div>
  <p class="abs small">Nemo enim ipsam voluptatem quia voluptas sit aspernatur aut odit aut fugit, sed quia consequuntur magni dolores eos qui ratione voluptatem sequi nesciunt.</p>
  <div class="abs author">- Daniel Reyes -</div>
</section>

<section class="news">
  <h2 class="section-title" style="top:2048px">LATEST TIPS AND NEWS</h2>
  <p class="section-sub" style="top:2103px">Lorem ipsum dolor sit amet, consectetuer. Proin gravida nibh vel velit auctor aliquetenean. Cum sociis Theme natoque penatibus et magnis dis parturient nascetur ridiculus mus.</p>

  <article class="abs news-card" style="left:132px">
    <div class="news-photo" role="img" aria-label="Nurse caring for an elderly woman"></div>
    <div class="date">OCT 27,2016</div>
    <h3>HEALTHCARE PLANNING</h3>
    <p class="small">Nemo enim ipsam voluptatem quia voluptas sit aspernatur aut odit aut fugit, sed quia consequuntur magni</p>
    <div class="byline"><span class="avatar" role="img" aria-label="Author portrait"></span>Lorem ipsum dolor sit amet</div>
  </article>
  <article class="abs news-card" style="left:455px">
    <div class="news-photo" role="img" aria-label="Team of smiling medical staff"></div>
    <div class="date">OCT 27,2016</div>
    <h3>HEALTHCARE PLANNING</h3>
    <p class="small">Nemo enim ipsam voluptatem quia voluptas sit aspernatur aut odit aut fugit, sed quia consequuntur magni</p>
    <div class="byline"><span class="avatar" role="img" aria-label="Author portrait"></span>Lorem ipsum dolor sit amet</div>
  </article>
  <article class="abs news-card" style="left:775px">
    <div class="news-photo" role="img" aria-label="Doctor holding a patient's hands"></div>
    <div class="date">OCT 27,2016</div>
    <h3>HEALTHCARE PLANNING</h3>
    <p class="small">Nemo enim ipsam voluptatem quia voluptas sit aspernatur aut odit aut fugit, sed quia consequuntur magni</p>
    <div class="byline"><span class="avatar" role="img" aria-label="Author portrait"></span>Lorem ipsum dolor sit amet</div>
  </article>
</section>

<footer class="site-footer">
  <div class="abs brand" style="top:58px"><span class="brand-mark"></span><span class="brand-name">Bright Harbor</span></div>
  <p class="abs small" style="left:132px;top:140px;width:300px">Lorem ipsum dolor sit amet, consectetuer. Proin gravida nibh vel velit auctor aliquet. Aenean sollicitudin, lorem</p>
  <div class="abs contact-line" style="left:132px;top:250px">
    <svg width="18" height="26" viewBox="0 0 18 26" fill="none" stroke="#2378c3" stroke-width="1.5"><rect x="2" y="1" width="14" height="24" rx="2"/><path d="M7 21h4"/></svg>
    <div>603-555-0142<br>info@brightharbormed.co</div>
  </div>
  <div class="abs contact-line" style="left:132px;top:320px">
    <svg width="20" height="26" viewBox="0 0 20 26" fill="none" stroke="#2378c3" stroke-width="1.5"><path d="M10 25s8-9 8-15a8 8 0 0 0-16 0c0 6 8 15 8 15z"/><circle cx="10" cy="10" r="3"/></svg>
    <div>12 Elm Street<br>Concord, NH 03301</div>
  </div>

  <h4 class="abs footer-head" style="left:466px;top:86px">LATEST TWEETS</h4>
  <div class="abs" style="left:466px;top:140px;width:240px">
    <div class="tweet"><span class="dot"></span><p class="small">Lorem ipsum dolor sit amet, consectetuer. Proin gravida nibh vel velit auctor aliquet. Aenean sollicitudin, lorem</p></div>
    <div class="divider" style="margin:14px 0 20px"></div>
    <div class="tweet"><span class="dot"></span><p class="small">Lorem ipsum dolor sit amet, consectetuer. Proin gravida nibh vel velit auctor aliquet. Aenean sollicitudin, lorem</p></div>
  </div>

  <h4 class="abs footer-head" style="left:777px;top:86px">RECENT POSTS</h4>
  <div class="abs" style="left:777px;top:140px;width:290px">
    <div class="post"><span class="avatar" role="img" aria-label="Author portrait"></span><p class="small">Lorem ipsum dolor sit amet, consectetuer. Proin gravida nibh vel velit auctor aliquet. Aenean sollicitudin, lorem</p></div>
    <div class="divider" style="margin:14px 0 20px"></div>
    <div class="post"><span class="avatar" role="img" aria-label="Author portrait"></span><p class="small">Lorem ipsum dolor sit amet, consectetuer. Proin gravida nibh vel velit auctor aliquet. Aenean sollicitudin, lorem</p></div>
  </div>
</footer>

<div class="bottom-bar">
  <div class="abs" style="left:132px;top:28px;font-size:9.5px;color:var(--text)">&copy;2016 brightharbormed.com. All rights reserved.</div>
  <div class="abs social"><span></span><span></span><span></span><span></span></div>
  <div class="abs partner"><i></i>lumenfold</div>
</div>

</body>
</html>
```